RTavenor Business Cards & Letterhead

I have a logo but need a design for some new business cards. We are a Design-Build Firm that specializes in the design and construction of commercial projects.
the cards need to be professional. no cartoon stuff.
i would like to have the cards in AI format so I can update the card as needed. Logo is provided.
Our Address is: 4187 Marlowe Ct. Apex, North Carolina 27614

```html
<!DOCTYPE html>
<html lang="en">
<head>
<meta charset="utf-8">
<title>RTavenor Business Card</title>
<link href="https://fonts.googleapis.com/css2?family=Lexend:wght@400;600;700&family=Figtree:wght@400;500&display=swap" rel="stylesheet">
<style>
  :root {
    --page-bg: #e4e4e4;
    --brand-blue: #175f96;
    --brand-blue-deep: #0f4a78;
    --brand-blue-light: #2a7fb8;
    --ink-gray: #48484a;
    --text-gray: #4b4b4d;
    --card-white: #f3f3f3;
    --tab-gray: #58585a;
  }
  html, body {
    margin: 0;
    width: 1200px;
    height: 1200px;
    overflow: hidden;
    background: var(--page-bg);
  }
  .canvas { position: relative; width: 1200px; height: 1200px; }
  .card {
    position: absolute;
    left: 234px;
    width: 731px;
    height: 418px;
    box-shadow: 0 10px 24px rgba(0,0,0,0.25);
  }
  .card-front { top: 160px; }
  .front-field {
    display: block; width: 100%; height: 100%;
  }
  .card-back {
    top: 632px;
    background: linear-gradient(100deg, #f4f4f4 0%, #ececec 100%);
    overflow: hidden;
  }
  .edge-tabs { position: absolute; right: 0; top: 0; width: 21px; height: 418px; }
  .wordmark {
    position: absolute; left: 56px; top: 56px;
    font-family: "Lexend", sans-serif; font-weight: 700;
    font-size: 44px; letter-spacing: -0.5px;
    color: var(--ink-gray); margin: 0; line-height: 1;
  }
  .person {
    position: absolute; right: 55px; top: 178px; text-align: right;
  }
  .person-name {
    font-family: "Lexend", sans-serif; font-weight: 600;
    font-size: 29px; color: var(--brand-blue); margin: 0; line-height: 1.1;
  }
  .person-role {
    font-family: "Figtree", sans-serif; font-size: 19px;
    color: var(--text-gray); margin: 6px 0 0; line-height: 1;
  }
  .address {
    position: absolute; left: 56px; top: 228px; margin: 0;
    font-family: "Figtree", sans-serif; font-size: 20px; line-height: 27px;
    color: var(--text-gray); font-style: normal;
  }
  .contact-list {
    position: absolute; left: 56px; top: 282px; margin: 0; padding: 0; list-style: none;
    font-family: "Figtree", sans-serif; font-size: 20px; color: var(--text-gray);
  }
  .contact-list li { display: flex; align-items: center; height: 27.5px; }
  .contact-list svg { width: 16px; height: 16px; margin-right: 9px; fill: var(--brand-blue); }
</style>
</head>
<body>
<main class="canvas">
  <section class="card card-front">
    <svg class="front-field" viewBox="0 0 731 418" preserveAspectRatio="none" role="img" aria-label="Blue embossed repeating brand pattern">
      <defs>
        <linearGradient id="frontGrad" x1="0" y1="1" x2="1" y2="0">
          <stop offset="0" stop-color="#124a74"/>
          <stop offset="0.55" stop-color="#1868a0"/>
          <stop offset="1" stop-color="#2c82b8"/>
        </linearGradient>
      </defs>
      <rect width="731" height="418" fill="url(#frontGrad)"/>
    </svg>
  </section>

  <section class="card card-back">
    <svg class="edge-tabs" viewBox="0 0 21 418">
      <path d="M0 0 H21 V165 H12 A12 12 0 0 1 0 153 Z" fill="var(--brand-blue)"/>
      <path d="M12 178 H21 V238 H12 A12 12 0 0 1 0 226 V190 A12 12 0 0 1 12 178 Z" fill="var(--tab-gray)"/>
      <path d="M12 250 H21 V418 H0 V262 A12 12 0 0 1 12 250 Z" fill="var(--brand-blue)"/>
    </svg>

    <h1 class="wordmark">RTAVENOR</h1>

    <div class="person">
      <p class="person-name">Russell Tavenor</p>
      <p class="person-role">President</p>
    </div>

    <address class="address">4187 Marlowe Ct. Apex,<br>North Carolina 27614</address>

    <ul class="contact-list">
      <li>
        <svg viewBox="0 0 24 24"><path d="M6.6 10.8a15 15 0 0 0 6.6 6.6l2.2-2.2a1 1 0 0 1 1-.25 11.4 11.4 0 0 0 3.6.57 1 1 0 0 1 1 1V20a1 1 0 0 1-1 1A17 17 0 0 1 3 4a1 1 0 0 1 1-1h3.5a1 1 0 0 1 1 1c0 1.25.2 2.45.57 3.57a1 1 0 0 1-.25 1z"/></svg>
        (919)-555-0147
      </li>
      <li>
        <svg viewBox="0 0 24 24"><path d="M2 5h20v14H2z M3 6l9 7 9-7" fill="var(--brand-blue)" stroke="#f0f0f0" stroke-width="1.5"/></svg>
        info@rtavenor.com
      </li>
      <li>
        <svg viewBox="0 0 24 24"><circle cx="12" cy="12" r="10"/><path d="M2 12h20M12 2c3 3 3 17 0 20M12 2c-3 3-3 17 0 20" stroke="#f0f0f0" stroke-width="1.4" fill="none"/></svg>
        www.rtavenor.com
      </li>
    </ul>
  </section>
</main>
</body>
</html>
```